Process Serving Company needs a letterhead design

Looking to have a letterhead designed for letters to attorneys advertising our business. We would like something eye catching but professional. Colors and logos are attached. Please add "Process Service and Attorney Support" near the logo or header

Target Market(s)

Attorneys

Font styles to use
Serif
Sans Serif

Colors
33a6d7
0255a3
85cae6
cee9f5
ecf7fb

```html
<!DOCTYPE html>
<html lang="en">
<head>
<meta charset="utf-8">
<title>Swiftwrit Process Letterhead</title>
<link rel="stylesheet" href="https://fonts.googleapis.com/css2?family=Source+Sans+3:wght@400;600&family=Open+Sans:wght@400&family=Arimo:wght@700&display=swap">
<style>
  :root {
    --sky: #33a6d7;
    --navy: #0255a3;
    --mist: #85cae6;
    --paper: #f9f9f9;
    --backdrop: #e6e6e6;
    --ink: #4a4a4a;
    --ink-dark: #3a3a3a;
  }
  * { margin: 0; padding: 0; box-sizing: border-box; }
  html, body { width: 1059px; height: 1200px; overflow: hidden; }
  body { background: var(--backdrop); position: relative; font-family: "Source Sans 3", sans-serif; }
  .letterhead {
    position: absolute; left: 119px; top: 20px;
    width: 821px; height: 1160px;
    background: var(--paper); overflow: hidden;
  }
  .top-band { position: absolute; left: 0; top: 0; width: 100%; height: 10px; background: var(--sky); }
  .brand { position: absolute; left: 69px; top: 42px; display: flex; align-items: center; gap: 12px; }
  .brand-square { width: 50px; height: 50px; background: var(--sky); }
  .brand-name {
    font-family: "Source Sans 3", sans-serif; font-weight: 400;
    color: var(--sky); font-size: 26px; line-height: 27px; letter-spacing: 0.5px;
    text-transform: uppercase;
  }
  .contact {
    position: absolute; left: 620px; top: 40px;
    font-family: "Source Sans 3", sans-serif; font-size: 11.5px; line-height: 16px; color: var(--ink-dark);
  }
  .contact-row { display: flex; align-items: center; gap: 6px; }
  .contact-row svg { width: 11px; height: 10px; fill: var(--sky); }
  .address { margin-top: 4px; padding-left: 11px; border-left: 2px solid var(--sky); margin-left: 4px; }
  .letter-body { position: absolute; left: 69px; top: 277px; width: 689px; color: var(--ink); }
  .salutation { font-family: "Arimo", sans-serif; font-weight: 700; font-size: 18.5px; color: #555; margin-bottom: 19px; }
  .letter-body p.copy { font-size: 16.3px; line-height: 21.5px; text-align: justify; margin-bottom: 21px; }
  .signature { position: absolute; left: 71px; top: 690px; width: 154px; height: 73px; background: linear-gradient(90deg, #e9e9e9, #dcdcdc); border-radius: 4px; }
  .footer-wave { position: absolute; left: 0; bottom: 0; width: 100%; height: 67px; }
  .website {
    position: absolute; left: 0; width: 100%; top: 1115px; text-align: center;
    font-family: "Open Sans", sans-serif; font-size: 12px; letter-spacing: 1.6px; color: var(--ink-dark);
  }
</style>
</head>
<body>
  <main class="letterhead">
    <div class="top-band"></div>

    <header class="brand">
      <div class="brand-square"></div>
      <div class="brand-name">Swiftwrit<br>Process</div>
    </header>

    <address class="contact" style="font-style:normal">
      <div class="contact-row"><svg viewBox="0 0 12 10"><path d="M1 3 Q6 -1 11 3 L9 5 L8 3 H4 L3 5 Z M3 5 H9 L10 9 H2 Z"/></svg>555-201-4830</div>
      <div class="contact-row"><svg viewBox="0 0 12 10"><path d="M2 5 L3 2 H9 L10 5 H11 V8 H1 V5 Z M2 8 H4 V10 H2 Z M8 8 H10 V10 H8 Z"/></svg>555-201-4871</div>
      <div class="contact-row"><svg viewBox="0 0 12 10"><path d="M1 3 L6 0 L11 3 V9 H1 Z M2 4 L6 7 L10 4 V8 H2 Z" fill-rule="evenodd"/></svg>hello@swiftwrit.com</div>
      <div class="address">4410 E Canyon Ave #210<br>Mesa Ridge AZ 85001</div>
    </address>

    <section class="letter-body">
      <p class="salutation">Dear Mr. Harlan,</p>
      <p class="copy">Lorem Ipsum is simply dummy text of the printing and typesetting industry. Lorem Ipsum has been the industry's standard dummy text ever since the 1500s, when an unknown printer took a galley of type and scrambled it to make a type specimen book. It has survived not only five centuries, but also the leap into electronic typesetting, remaining essentially unchanged.</p>
      <p class="copy">The standard chunk of Lorem Ipsum used since the 1500s is reproduced below for those interested. Sections 1.10.32 and 1.10.33 from "de Finibus Bonorum et Malorum" by Marcus Tellan are also reproduced in their exact original form, accompanied by English versions from the 1914 translation by H. Corwell</p>
      <p class="copy">Lorem Ipsum is simply dummy text of the printing and typesetting industry. Lorem Ipsum has been the industry's standard dummy text ever since the 1500s, when an unknown printer took a galley of type and scrambled it to make a type specimen book. It has survived not only five centuries, but also the leap into electronic typesetting, remaining essentially unchanged. It was popularised in the</p>
    </section>

    <div class="signature" role="img" aria-label="Handwritten signature of the sender"></div>

    <svg class="footer-wave" viewBox="0 0 924 75" preserveAspectRatio="none" aria-hidden="true">
      <path d="M0 5 Q462 80 924 0 L924 3 Q462 74 0 24 Z" fill="var(--sky)"/>
      <path d="M0 34 Q462 98 924 5 L924 75 L0 75 Z" fill="var(--navy)"/>
    </svg>
    <div class="website">www.swiftwrit.com</div>
  </main>
</body>
</html>
```